Moravel Aesthetic Doctor

I require an elegant, luxurious looking business card for my aesthetic business. I am a doctor and that will set me aside from competitors. I am planning to provide home and spa based treatments to clients with high expectations. I have attached my logo.

```html
<!DOCTYPE html>
<html lang="en">
<head>
<meta charset="utf-8">
<title>Moravel Aesthetic Doctor – Business Card</title>
<link rel="stylesheet" href="https://fonts.googleapis.com/css2?family=Roboto:ital,wght@0,300;0,400;1,400&display=swap">
<style>
  :root {
    --backdrop: #3a3a3c;
    --card: #1f1f21;
    --card-edge: #2a2a2d;
    --silver: #a9abaf;
    --text-light: #c9cacd;
    --accent: #4fb3e8;
  }
  * { box-sizing: border-box; margin: 0; padding: 0; }
  html, body {
    width: 799px; height: 1200px; overflow: hidden;
    background: var(--backdrop);
    font-family: "Roboto", Arial, sans-serif;
  }
  .sheet {
    position: relative; width: 799px; height: 1200px;
    display: flex; flex-direction: column; align-items: center; justify-content: space-around;
    padding: 70px 0;
  }
  .card {
    position: relative; width: 580px; height: 331px;
    background: var(--card);
    border: 1px solid var(--card-edge);
    border-radius: 4px;
    box-shadow: 0 14px 30px rgba(0,0,0,.45);
  }
  /* Front */
  .card--front { display: flex; align-items: center; justify-content: center; }
  .front-mark { display: flex; align-items: center; gap: 16px; }
  .front-mark__ring {
    width: 40px; height: 40px; border-radius: 50%;
    border: 3px solid var(--silver);
  }
  .front-mark__name {
    font-weight: 300; font-size: 30px; letter-spacing: 4px;
    color: var(--silver); text-transform: uppercase;
  }
  /* Back */
  .profile { position: absolute; left: 40px; top: 40px; }
  .profile__name { font-weight: 300; font-size: 22px; color: var(--text-light); }
  .profile__letters { font-style: italic; font-size: 10px; color: var(--accent); margin-top: 6px; }
  .profile__diploma { font-size: 14px; color: var(--accent); margin-top: 4px; }

  .contacts { position: absolute; left: 40px; bottom: 40px; list-style: none; }
  .contacts li {
    display: flex; align-items: center; gap: 10px;
    font-size: 14px; color: var(--accent); line-height: 22px;
  }
  .contacts svg { width: 12px; height: 12px; fill: var(--accent); }
  .contacts__social { gap: 6px !important; }
  .social-dot {
    width: 14px; height: 14px; border-radius: 50%; background: var(--accent);
  }

  .brand { position: absolute; right: 36px; bottom: 44px; display: flex; align-items: center; gap: 12px; }
  .brand__ring { width: 44px; height: 44px; border-radius: 50%; border: 2px solid var(--text-light); }
  .brand__name {
    font-weight: 300; font-size: 24px; letter-spacing: 2px; line-height: 1.05;
    color: var(--text-light); text-transform: uppercase;
  }
  .brand__name span { display: block; font-size: 15px; letter-spacing: 3px; }
</style>
</head>
<body>
<main class="sheet">
  <section class="card card--front" aria-label="Card front">
    <div class="front-mark">
      <div class="front-mark__ring"></div>
      <div class="front-mark__name">Moravel</div>
    </div>
  </section>

  <section class="card card--back" aria-label="Card back">
    <div class="profile">
      <div class="profile__name">Dr Elise Varden</div>
      <div class="profile__letters">MRCPCH MD</div>
      <div class="profile__diploma">Australasian Diploma of Aesthetic Medicine</div>
    </div>

    <ul class="contacts">
      <li>
        <svg viewBox="0 0 24 24"><path d="M6.6 10.8a15.1 15.1 0 0 0 6.6 6.6l2.2-2.2c.3-.3.7-.4 1-.2 1.1.4 2.3.6 3.6.6.6 0 1 .4 1 1V20c0 .6-.4 1-1 1A17 17 0 0 1 3 4c0-.6.4-1 1-1h3.5c.6 0 1 .4 1 1 0 1.3.2 2.5.6 3.6.1.3 0 .7-.2 1z"/></svg>
        0800 555 014
      </li>
      <li>
        <svg viewBox="0 0 24 24"><path d="M2 5h20v14H2z M2 5l10 8 10-8" fill="none" stroke="#4fb3e8" stroke-width="2"/></svg>
        elise@moravel.co.nz
      </li>
      <li>
        <svg viewBox="0 0 24 24"><circle cx="12" cy="12" r="9" fill="none" stroke="#4fb3e8" stroke-width="2"/><path d="M3 12h18M12 3c3 3 3 15 0 18M12 3c-3 3-3 15 0 18" fill="none" stroke="#4fb3e8" stroke-width="1.6"/></svg>
        www.moravel.co.nz
      </li>
      <li class="contacts__social">
        Follow us on:
        <span class="social-dot"></span>
        <span class="social-dot"></span>
      </li>
    </ul>

    <div class="brand">
      <div class="brand__ring"></div>
      <div class="brand__name">Moravel<span>Aesthetic Doctor</span></div>
    </div>
  </section>
</main>
</body>
</html>
```